VR7K Coding Courses Email Marketing Campaign

We are looking for someone to provide 4 email campaigns to publish in the month of October. The campaign will be sent via postvenn and must include an commerce solution, incorporate our commercial, brochure and registration form.
Important things to highlight in the design content:
BTQE Approved Education Provider
Enhanced curriculum with DRELO domains
Affordable cost with payment plans
Name Brand Learning Management System- Pavix
Flexible learning with instructor led or self paced courses
Job placement opportunities with VR7 Wellness Care Partners

```html
<!DOCTYPE html>
<html lang="en">
<head>
<meta charset="utf-8">
<title>VR7K Coding Courses</title>
<link rel="stylesheet" href="https://fonts.googleapis.com/css2?family=Montserrat:wght@500;600;700&family=Mulish:wght@400;500&display=swap">
<style>
  :root {
    --purple: #5a1a9c;
    --purple-deep: #4b1589;
    --green: #72b626;
    --ink: #555555;
    --muted: #8f8f8f;
    --panel: #ececec;
    --rule: #e3e3e3;
    --white: #ffffff;
  }
  * { box-sizing: border-box; margin: 0; padding: 0; }
  html, body { width: 712px; height: 1200px; overflow: hidden; background: var(--white); }
  body { font-family: "Mulish", Arial, sans-serif; color: var(--ink); text-align: center; }
  .heading-font { font-family: "Montserrat", Arial, sans-serif; }

  .masthead { height: 100px; display: flex; align-items: center; justify-content: center; }
  .brand-name { font-family: "Montserrat", Arial, sans-serif; font-weight: 600; font-size: 56px; color: var(--purple); letter-spacing: 1px; }
  .masthead-rule { height: 5px; background: var(--green); }

  .hero { height: 318px; background: linear-gradient(120deg, #2b1a24 0%, #c02a7e 30%, #e6739c 48%, #e0a64a 62%, #8f9a2b 78%, #3a1d2a 100%); }

  .intro { height: 139px; padding-top: 17px; }
  .intro h1 { font-family: "Montserrat", Arial, sans-serif; font-weight: 700; font-size: 22px; color: var(--ink); }
  .intro h1 span { color: var(--green); }
  .intro p { font-size: 11px; line-height: 18px; color: var(--muted); width: 400px; margin: 8px auto 0; }
  .intro .cta-line { font-family: "Montserrat", Arial, sans-serif; font-weight: 600; font-size: 15px; color: var(--purple); margin-top: 8px; }

  .benefits { background: var(--panel); height: 408px; padding-top: 14px; }
  .benefits h2 { font-family: "Montserrat", Arial, sans-serif; font-weight: 700; font-size: 21px; color: var(--purple); }
  .benefits p { font-size: 11px; line-height: 17px; color: var(--muted); width: 400px; margin: 8px auto 0; }
  .tile-grid { display: grid; grid-template-columns: repeat(3, 135px); gap: 8px 7px; width: 419px; margin: 18px auto 0; }
  .tile { height: 116px; background: linear-gradient(160deg, #6e26b0, var(--purple-deep)); position: relative; color: var(--white); }
  .tile svg { position: absolute; left: 50%; top: 12px; transform: translateX(-50%); }
  .tile-label { position: absolute; left: 0; right: 0; bottom: 12px; font-family: "Montserrat", Arial, sans-serif; font-weight: 700; font-size: 12px; line-height: 18px; }
  .register { display: block; width: 117px; height: 28px; margin: 20px auto 0; border-radius: 14px; background: var(--green); color: var(--white); font-family: "Montserrat", Arial, sans-serif; font-weight: 700; font-size: 13px; line-height: 28px; text-decoration: none; }

  .contact { padding-top: 13px; font-family: "Montserrat", Arial, sans-serif; }
  .brochure { color: var(--green); font-weight: 600; font-size: 13px; line-height: 21px; }
  .site { color: var(--purple); font-weight: 600; font-size: 13px; line-height: 21px; }
  .divider { width: 392px; height: 1px; background: var(--rule); margin: 9px auto 0; }
  .questions { color: var(--green); font-weight: 700; font-size: 13px; margin-top: 8px; line-height: 18px; }
  .detail { font-family: "Mulish", Arial, sans-serif; font-size: 12.5px; line-height: 21px; color: var(--ink); }
  .detail b { font-family: "Montserrat", Arial, sans-serif; color: var(--purple); font-weight: 700; }
  .follow { color: var(--green); font-weight: 600; font-size: 13px; margin-top: 20px; }
  .social { display: flex; justify-content: center; gap: 4px; margin-top: 4px; }
  .social span { width: 17px; height: 17px; border-radius: 50%; background: #6a6a6a; }
</style>
</head>
<body>
  <header class="masthead">
    <div class="brand-name">VR7K</div>
  </header>
  <div class="masthead-rule"></div>

  <div class="hero" role="img" aria-label="Photo of a smiling woman in green sunglasses covered in colourful festival powder"></div>

  <section class="intro">
    <h1>START YOUR CODING <span>CAREER TODAY</span></h1>
    <p>Coding is one of the fastest, growing careers in the industry today. An average salary of a coder is $50,000 with around 3 years of experience. Coders have the flexibility to work from home with endless advancement opportunities.</p>
    <div class="cta-line">What are you waiting for?&nbsp; Enroll today!</div>
  </section>

  <section class="benefits">
    <h2>WHY VR7?</h2>
    <p>We have invested a lot of time and resources to ensure our coding program not only prepares you to pass the test the first time but to be job ready.<br>Our next class starts October 31st.</p>
    <div class="tile-grid">
      <div class="tile"><svg width="40" height="40" viewBox="0 0 40 40"><circle cx="20" cy="20" r="16" fill="none" stroke="#fff" stroke-width="2.5"/></svg><div class="tile-label">BTQE APPROVED</div></div>
      <div class="tile"><svg width="40" height="40" viewBox="0 0 40 40"><circle cx="20" cy="20" r="16" fill="none" stroke="#fff" stroke-width="2.5"/></svg><div class="tile-label" style="bottom:14px">DRELO DOMAINS</div></div>
      <div class="tile"><svg width="40" height="40" viewBox="0 0 40 40"><circle cx="20" cy="20" r="16" fill="none" stroke="#fff" stroke-width="2.5"/></svg><div class="tile-label" style="bottom:14px">PAYMENT PLANS</div></div>
      <div class="tile"><svg width="40" height="40" viewBox="0 0 40 40"><circle cx="20" cy="20" r="16" fill="none" stroke="#fff" stroke-width="2.5"/></svg><div class="tile-label">JOB PLACEMENT</div></div>
      <div class="tile"><svg width="40" height="40" viewBox="0 0 40 40"><circle cx="20" cy="20" r="16" fill="none" stroke="#fff" stroke-width="2.5"/></svg><div class="tile-label" style="bottom:2px">FLEXBILE ONLINE<br>COURSES</div></div>
      <div class="tile"><svg width="40" height="40" viewBox="0 0 40 40"><circle cx="20" cy="20" r="16" fill="none" stroke="#fff" stroke-width="2.5"/></svg><div class="tile-label">LMS: PAVIX</div></div>
    </div>
    <a class="register" href="#">REGISTER</a>
  </section>

  <footer class="contact">
    <div class="brochure">Click here to download our brochure</div>
    <div class="site">www.vr7wellnesscare.com</div>
    <div class="divider"></div>
    <div class="questions">STILL HAVE QUESTIONS?</div>
    <div class="detail">2180 Harlow Ridge Drive, STE 105, Brenford, TX 70418</div>
    <div class="detail"><b>Email :</b> academy@vr7wellnesscare.com</div>
    <div class="detail"><b>Call :</b> (555) 014-2297</div>
    <div class="divider"></div>
    <div class="follow">Follow us</div>
    <div class="social">
      <span role="img" aria-label="Social profile"></span>
      <span role="img" aria-label="Social profile"></span>
      <span role="img" aria-label="Social profile"></span>
    </div>
  </footer>
</body>
</html>
```